Need help in designing new business card utilizing our new logo.

BuildMark Solutions works with Construction Business Owners, Managers & IT Professionals to strengthen software usage and increase user productivity.

Our Construction Accounting and Mobile Field Management Software Clients engage with us in the following areas:

New Software Implementations
Software Re-Implementations
Redesigning Software Usage at the User Level
Project Coordination & Management
Continued Software Support

Old tag line:
Weighing Options - Implementing Solutions

www.buildmark-solutions.example

Ridge 4 is a product, but not needed for a new business card.

```html
<!DOCTYPE html>
<html lang="en">
<head>
<meta charset="utf-8">
<title>BuildMark Solutions – Business Card</title>
<link href="https://fonts.googleapis.com/css2?family=Roboto:wght@400;500&family=Roboto+Condensed:wght@700&display=swap" rel="stylesheet">
<style>
  :root {
    --brand-blue: #1015a0;
    --text-dark: #2f2f33;
    --text-grey: #9a9a9e;
    --card-bg: #f1f1f2;
    --page-bg: #c4c4c6;
    --band-text: #ffffff;
  }
  * { box-sizing: border-box; margin: 0; padding: 0; }
  html, body {
    width: 1200px; height: 576px; overflow: hidden;
    background: var(--page-bg);
    font-family: "Roboto", Arial, sans-serif;
  }
  .canvas { position: relative; width: 1200px; height: 576px; }

  .card {
    position: absolute;
    width: 484px; height: 292px;
    background: var(--card-bg);
    border-radius: 12px;
    overflow: hidden;
  }
  .card--front { left: 82px; top: 138px; }
  .card--back  { left: 602px; top: 138px; }

  /* Brand name lockup */
  .brand {
    display: flex; align-items: center; gap: 10px;
    color: var(--brand-blue);
    font-family: "Roboto", Arial, sans-serif;
    font-weight: 500;
    font-size: 27px;
    letter-spacing: 0.5px;
    white-space: nowrap;
  }
  .brand__square { width: 22px; height: 22px; background: var(--brand-blue); flex: none; }

  /* Front */
  .card--front .brand { position: absolute; top: 72px; left: 0; right: 0; justify-content: center; }
  .services-band {
    position: absolute; left: 0; top: 167px; width: 100%; height: 80px;
    background: var(--brand-blue);
    color: var(--band-text);
    font-size: 13px; line-height: 18.5px;
    text-align: center;
    padding-top: 13px;
  }
  .services-band .sep { margin: 0 9px; }
  .front-url {
    position: absolute; left: 0; right: 0; top: 262px;
    display: flex; justify-content: center; align-items: center; gap: 18px;
    color: var(--brand-blue); font-size: 12px;
  }
  .front-url::before, .front-url::after {
    content: ""; width: 44px; height: 1px; background: var(--text-grey);
  }

  /* Back */
  .tagline-strip {
    position: absolute; left: 0; top: 0; width: 40px; height: 100%;
    background: var(--brand-blue);
  }
  .tagline-strip span {
    position: absolute; left: 50%; top: 50%;
    transform: translate(-50%, -50%) rotate(-90deg);
    white-space: nowrap;
    color: var(--band-text); font-size: 11.5px;
  }
  .card--back .brand { position: absolute; left: 66px; top: 48px; }
  .person { position: absolute; left: 66px; top: 118px; }
  .person__name {
    font-family: "Roboto Condensed", "Arial Narrow", sans-serif;
    font-weight: 700; font-size: 22px; color: var(--brand-blue);
  }
  .person__role { font-size: 11.5px; color: var(--text-dark); margin-top: 2px; }

  .contacts { position: absolute; left: 66px; top: 183px; list-style: none; }
  .contacts li {
    display: flex; align-items: center; gap: 9px;
    font-size: 12px; color: var(--text-dark); height: 17px;
  }
  .contacts svg { width: 11px; height: 11px; fill: var(--brand-blue); flex: none; }
  .contacts .accent { color: var(--brand-blue); }
  .address { position: absolute; left: 66px; top: 257px; font-size: 12px; color: var(--text-dark); }
</style>
</head>
<body>
<main class="canvas">

  <section class="card card--front" aria-label="Business card front">
    <div class="brand"><span class="brand__square"></span>BuildMark Solutions</div>
    <div class="services-band">
      <p>New Software Implementations<span class="sep">|</span>Software Re-Implementations</p>
      <p>Redesigning Software Usage at the User Level</p>
      <p>Project Coordination &amp; Management<span class="sep">|</span>Continued Software Support</p>
    </div>
    <p class="front-url">www.buildmark-solutions.example</p>
  </section>

  <section class="card card--back" aria-label="Business card back">
    <div class="tagline-strip"><span>Weighing Options - Implementing Solutions</span></div>
    <div class="brand"><span class="brand__square"></span>BuildMark Solutions</div>
    <div class="person">
      <h1 class="person__name">Dana R. Whitfield</h1>
      <p class="person__role">Owner</p>
    </div>
    <ul class="contacts">
      <li>
        <svg viewBox="0 0 12 12" aria-hidden="true"><path d="M3 0h6a1 1 0 0 1 1 1v10a1 1 0 0 1-1 1H3a1 1 0 0 1-1-1V1a1 1 0 0 1 1-1zm0.8 1.5v7.5h4.4V1.5zM6 9.6a.7.7 0 1 0 0 1.4.7.7 0 0 0 0-1.4z"/></svg>
        555-014-2290
      </li>
      <li>
        <svg viewBox="0 0 12 12" aria-hidden="true"><path d="M0 4c0-1.5 2.5-2.5 6-2.5S12 2.5 12 4v1H9V3.8H3V5H0zM2.5 6h7l1.5 5H1z"/></svg>
        800-555-0137 ext. 100
      </li>
      <li>
        <svg viewBox="0 0 12 12" aria-hidden="true"><path d="M0 2h12v1L6 7 0 3zM0 4.2l6 4 6-4V10H0z"/></svg>
        dana.whitfield@buildmark-solutions.example
      </li>
      <li>
        <svg viewBox="0 0 12 12" aria-hidden="true"><path d="M6 0a6 6 0 1 0 0 12A6 6 0 0 0 6 0zm-.6 1.3v2.1H3.6c.4-1 1-1.8 1.8-2.1zm1.2 0c.8.3 1.4 1.1 1.8 2.1H6.6zM1.6 4.6h1.7a9 9 0 0 0 0 2.8H1.6a4.7 4.7 0 0 1 0-2.8zm2.9 0h3a8 8 0 0 1 0 2.8h-3a8 8 0 0 1 0-2.8zm4.2 0h1.7a4.7 4.7 0 0 1 0 2.8H8.7a9 9 0 0 0 0-2.8zM3.6 8.6h1.8v2.1c-.8-.3-1.4-1.1-1.8-2.1zm3 0h1.8c-.4 1-1 1.8-1.8 2.1z"/></svg>
        www.<span class="accent">buildmark-solutions</span>.example
      </li>
    </ul>
    <p class="address">14B Harbor Lane - Suite 310 Millbrook, NY 10000</p>
  </section>

</main>
</body>
</html>
```